Velmora Freightway Solutions Business cards

Would like a very unique design catchy but professional for business cards. Please use log provided.Marlon WellsCeo and Founder TransCon Logistix Solutions1-888-913-3225mwells@tlsolutionsus.comwww.tlsolutionsus.com

```html
<!DOCTYPE html>
<html lang="en">
<head>
<meta charset="utf-8">
<title>Velmora Freightway Solutions – Business Cards</title>
<link rel="stylesheet" href="https://fonts.googleapis.com/css2?family=Montserrat:wght@600;700;800&family=Open+Sans:wght@400;600&display=swap">
<style>
  :root{
    --backdrop:#efe6d6;
    --brand-blue:#1276bd;
    --brand-red:#e5202e;
    --ink:#1d1d1f;
    --paper:#ffffff;
  }
  *{margin:0;padding:0;box-sizing:border-box}
  html,body{width:1200px;height:895px;overflow:hidden}
  body{background:var(--backdrop);font-family:"Open Sans",sans-serif;position:relative}
  .card{
    position:absolute;top:148px;width:344px;height:600px;border-radius:30px;
    box-shadow:0 10px 24px rgba(0,0,0,.18);
  }
  /* back side */
  .card--back{left:214px;background:var(--brand-blue);}
  .back-brand{
    position:absolute;left:0;right:0;bottom:70px;text-align:center;color:var(--paper);
  }
  .back-brand__mark{display:block;width:26px;height:26px;margin:0 auto 18px;background:var(--paper)}
  .back-brand__name{
    font-family:"Montserrat",sans-serif;font-weight:700;font-size:22px;line-height:1.3;
    letter-spacing:2px;text-transform:uppercase;
  }
  .back-brand__rule{display:block;width:190px;height:2px;margin:16px auto 0;background:var(--paper)}
  /* front side */
  .card--front{
    left:642px;background:var(--paper);border:9px solid var(--brand-blue);
    padding:56px 34px 44px;display:flex;flex-direction:column;align-items:center;text-align:center;
  }
  .front-brand{display:flex;align-items:center;gap:12px;margin-bottom:60px}
  .front-brand__mark{width:30px;height:30px;background:var(--brand-red);flex:none}
  .front-brand__name{
    font-family:"Montserrat",sans-serif;font-weight:700;font-size:20px;line-height:1.25;
    color:var(--brand-blue);text-align:left;
  }
  .person__name{
    font-family:"Montserrat",sans-serif;font-weight:800;font-size:27px;letter-spacing:2px;
    color:var(--brand-red);text-transform:uppercase;
  }
  .person__title{font-size:16px;color:var(--ink);margin-top:6px}
  .person__company{font-size:16px;color:var(--brand-blue);margin-top:4px}
  .divider{display:flex;align-items:center;gap:8px;margin:36px 0 30px;width:100%}
  .divider__line{flex:1;height:2px;background:var(--brand-blue)}
  .icon{width:30px;height:30px;flex:none}
  .contacts{list-style:none;font-size:16px;color:var(--ink);line-height:1.7}
</style>
</head>
<body>
  <section class="card card--back" aria-label="Card back">
    <div class="back-brand">
      <span class="back-brand__mark"></span>
      <p class="back-brand__name">Velmora<br>Freightway<br>Solutions</p>
      <span class="back-brand__rule"></span>
    </div>
  </section>

  <section class="card card--front" aria-label="Card front">
    <div class="front-brand">
      <span class="front-brand__mark"></span>
      <p class="front-brand__name">Velmora Freightway<br>Solutions</p>
    </div>

    <h1 class="person__name">Dorian Pike</h1>
    <p class="person__title">CEO and Founder</p>
    <p class="person__company">Velmora Freightway Solutions</p>

    <div class="divider">
      <span class="divider__line"></span>
      <svg class="icon" viewBox="0 0 30 30" aria-label="Phone"><circle cx="15" cy="15" r="13" fill="none" stroke="#1276bd" stroke-width="2"/><circle cx="15" cy="15" r="9" fill="#e5202e"/><path d="M11.5 11c.5 3.5 4 7 7.5 7.5l1-1.6-2-1.2-.9.8c-1.3-.6-2.5-1.8-3.1-3.1l.8-.9-1.2-2z" fill="#fff"/></svg>
      <svg class="icon" viewBox="0 0 30 30" aria-label="Email"><circle cx="15" cy="15" r="13" fill="none" stroke="#1276bd" stroke-width="2"/><circle cx="15" cy="15" r="9" fill="#e5202e"/><rect x="10" y="11.5" width="10" height="7" fill="#fff"/><path d="M10 11.5l5 4 5-4" fill="none" stroke="#e5202e" stroke-width="1"/></svg>
      <svg class="icon" viewBox="0 0 30 30" aria-label="Website"><circle cx="15" cy="15" r="13" fill="none" stroke="#1276bd" stroke-width="2"/><circle cx="15" cy="15" r="9" fill="#e5202e"/><circle cx="15" cy="15" r="5" fill="none" stroke="#fff" stroke-width="1.2"/><path d="M10 15h10M15 10c-2 3-2 7 0 10M15 10c2 3 2 7 0 10" fill="none" stroke="#fff" stroke-width="1"/></svg>
      <span class="divider__line"></span>
    </div>

    <ul class="contacts">
      <li>1-888-470-6158</li>
      <li>dpike@vfwayroutes.com</li>
      <li>www.vfwayroutes.com</li>
    </ul>
  </section>
</body>
</html>
```